BUSINESS CARD DESIGN

NAME- DALE VORSKIN
PHONE NUMER - 555- 714-9082
EMAIL- OFFICE@TRV-GROUNDMAKRZ.COM
BACK OF CARD- SPEACIALIZES IN LAND CLEARING, FORESTRY MUCLHING AND EXCAVATION

Contact Information for Business Card

NAME- DALE VORSKIN PHONE NUMER - 555- 714-9082 EMAIL- OFFICE@TRV-GROUNDMAKRZ.COM BACK OF CARD- SPEACIALIZES IN LAND CLEARING , MUCLHING AND EXCAVATION

```html
<!DOCTYPE html>
<html lang="en">
<head>
<meta charset="utf-8">
<title>Business Card – Terravale Groundmakrz</title>
<link href="https://fonts.googleapis.com/css2?family=Lato:wght@400;700;900&display=swap" rel="stylesheet">
<style>
  :root{
    --backdrop:#2a2b2e;
    --card:#141516;
    --yellow:#f6b115;
    --silver:#d4d5d7;
    --white:#f2f2f2;
    --ink:#141516;
    --rule:#4a4b4e;
  }
  *{box-sizing:border-box;margin:0;padding:0}
  html,body{width:1200px;height:952px;overflow:hidden}
  body{
    background:radial-gradient(ellipse at 60% 55%, #3a3b3e 0%, var(--backdrop) 55%, #1c1d1f 100%);
    font-family:"Lato",sans-serif;
    position:relative;
  }
  .card{
    position:absolute;
    width:540px;height:309px;
    background:var(--card);
    box-shadow:0 14px 30px rgba(0,0,0,.55);
    overflow:hidden;
  }
  .card--back{left:610px;top:110px}
  .card--front{left:60px;top:520px}

  /* brand block (name set in type with one circle) */
  .brand{display:flex;flex-direction:column;align-items:center;gap:10px;color:var(--silver);font-weight:700;text-align:center}
  .brand__circle{width:58px;height:58px;border-radius:50%;border:3px solid var(--silver)}
  .brand__name{font-size:22px;letter-spacing:2px;line-height:1.15}
  .brand__name span{display:block;font-size:13px;letter-spacing:4px}

  /* back */
  .card--back .brand{position:absolute;left:0;right:0;top:62px}
  .service-band{
    position:absolute;left:0;right:0;top:236px;height:24px;
    background:var(--yellow);color:var(--ink);
    font-weight:900;font-size:11px;letter-spacing:.3px;
    display:flex;align-items:center;gap:30px;padding-left:40px;
  }

  /* front */
  .edge-bar{position:absolute;background:var(--yellow)}
  .edge-bar--left{left:0;top:40px;width:14px;height:150px}
  .edge-bar--right{right:0;top:78px;width:22px;height:150px}
  .card--front .brand{position:absolute;left:30px;width:210px;top:78px}
  .divider{position:absolute;left:258px;top:92px;width:1px;height:140px;background:var(--rule)}
  .contact{position:absolute;left:282px;top:96px;color:var(--white)}
  .contact__name{font-size:25px;font-weight:700;letter-spacing:1px;line-height:1}
  .contact__name em{font-style:normal;color:var(--yellow)}
  .contact__title{font-size:14px;margin-top:6px;margin-bottom:14px}
  .contact__list{list-style:none;font-size:13px;line-height:22px}
  .contact__list li{display:flex;align-items:center;gap:7px}
  .contact__list svg{width:11px;height:11px;fill:var(--yellow);flex:none}
</style>
</head>
<body>

  <section class="card card--back" aria-label="Card back">
    <div class="brand">
      <div class="brand__circle"></div>
      <div class="brand__name">TERRAVALE<span>GROUNDMAKRZ LLC</span></div>
    </div>
    <div class="service-band">
      <span>• SPEACIALIZES IN LAND CLEARING</span>
      <span>• MUCLHING AND EXCAVATION</span>
    </div>
  </section>

  <section class="card card--front" aria-label="Card front">
    <div class="edge-bar edge-bar--left"></div>
    <div class="edge-bar edge-bar--right"></div>
    <div class="brand">
      <div class="brand__circle"></div>
      <div class="brand__name">TERRAVALE<span>GROUNDMAKRZ LLC</span></div>
    </div>
    <div class="divider"></div>
    <div class="contact">
      <h1 class="contact__name">DALE <em>VORSKIN</em></h1>
      <p class="contact__title">Managing Director</p>
      <ul class="contact__list">
        <li><svg viewBox="0 0 24 24" aria-hidden="true"><path d="M6.6 10.8a15 15 0 0 0 6.6 6.6l2.2-2.2c.3-.3.7-.4 1-.2 1.1.4 2.3.6 3.6.6.6 0 1 .4 1 1V20c0 .6-.4 1-1 1C10.6 21 3 13.4 3 4c0-.6.4-1 1-1h3.5c.6 0 1 .4 1 1 0 1.3.2 2.5.6 3.6.1.3 0 .7-.2 1z"/></svg>555- 714-9082</li>
        <li><svg viewBox="0 0 24 24" aria-hidden="true"><path d="M2 5h20v14H2z M3 6l9 7 9-7" fill="var(--yellow)"/><path d="M3 6l9 7 9-7" fill="none" stroke="#141516" stroke-width="2"/></svg>office@trv-groundmakrz.com</li>
        <li><svg viewBox="0 0 24 24" aria-hidden="true"><circle cx="12" cy="12" r="10"/><path d="M2 12h20M12 2c3 3 3 17 0 20M12 2c-3 3-3 17 0 20" fill="none" stroke="#141516" stroke-width="1.6"/></svg>www.trv-groundmakrz.com</li>
      </ul>
    </div>
  </section>

</body>
</html>
```